Laser Tattoo Removal Business Cards

We are looking for a professional business card design for a laser tattoo removal business. Ideally looking for a black business card design. The name of the business is Brightline Tattoo Removal. We place our cards at local tattoo shops so we ideally are looking for something trendy/edgy to draw both male and female clientele in.

Target Market(s)

Male/Female ages 18-60

Contact Information for Business Card

black background ideally.. hoping to stay within greys, whites and black

Font styles to use
Serif
Sans Serif

Colors
121212
a9a9a9
5c5c5c
f5f5f5
ffffff
7f7f7f
606060
848484
9d9d9d

Requirements
Must have
• Employee Info:
• Melissa Thornbury
• Chief Executive Offer
• m: 919.537.2846
• w: 919.362.4178
• f: 919.685.3907
• mthornbury@brightlinetattooremoval.example
• Address:
• 4615 Oakmere Pkwy, Suite 210
• Raleigh, NC 27654
• Website:
• www.brightlinetattooremoval.example
Nice to have
• Myabe business name on back or logo on back and employee info on the front

```html
<!DOCTYPE html>
<html lang="en">
<head>
<meta charset="utf-8">
<title>Brightline Tattoo Removal – Business Card</title>
<link rel="stylesheet" href="https://fonts.googleapis.com/css2?family=Oswald:wght@400;500&family=Roboto:wght@400;500;700&display=swap">
<style>
  :root {
    --ink: #121212;
    --slate: #5c5c5c;
    --mid-grey: #7f7f7f;
    --soft-grey: #a9a9a9;
    --paper: #f5f5f5;
    --white: #ffffff;
    --backdrop: #d9d6d2;
    --logo-block: #2b2b2b;
  }
  * { box-sizing: border-box; margin: 0; padding: 0; }
  html, body {
    width: 1200px;
    height: 969px;
    overflow: hidden;
  }
  body {
    background: var(--backdrop);
    position: relative;
    font-family: "Roboto", Arial, sans-serif;
  }
  .business-card {
    position: absolute;
    left: 100px;
    top: 200px;
    width: 1000px;
    height: 568px;
    background: linear-gradient(135deg, #eeeeec 0%, var(--paper) 45%, #e9e8e6 100%);
    border: 1px solid rgba(255, 255, 255, 0.9);
    box-shadow: 0 2px 10px rgba(0, 0, 0, 0.12);
  }
  .brand-block {
    position: absolute;
    left: 60px;
    top: 0;
    width: 212px;
    height: 218px;
    background: var(--logo-block);
    clip-path: polygon(0 0, 100% 0, 100% 100%, 26px 100%, 0 calc(100% - 26px));
    display: flex;
    align-items: center;
    justify-content: center;
    text-align: center;
  }
  .brand-name {
    font-family: "Oswald", "Arial Narrow", sans-serif;
    font-weight: 400;
    font-size: 30px;
    line-height: 1.15;
    letter-spacing: 2px;
    text-transform: uppercase;
    color: var(--white);
  }
  .employee-name {
    position: absolute;
    left: 301px;
    top: 128px;
    font-family: "Oswald", "Arial Narrow", sans-serif;
    font-weight: 400;
    font-size: 52px;
    line-height: 1;
    letter-spacing: 1px;
    text-transform: uppercase;
    color: var(--ink);
  }
  .employee-title {
    position: absolute;
    left: 302px;
    top: 200px;
    font-size: 21px;
    font-weight: 500;
    letter-spacing: 0.6px;
    text-transform: uppercase;
    color: var(--slate);
  }
  .contact-details {
    position: absolute;
    right: 57px;
    top: 308px;
    text-align: right;
    font-size: 22px;
    line-height: 31px;
    color: var(--ink);
    font-style: normal;
  }
  .contact-details .address { margin-bottom: 5px; }
  .contact-details strong { font-weight: 700; }
</style>
</head>
<body>
  <section class="business-card" aria-label="Business card">
    <div class="brand-block">
      <span class="brand-name">Brightline<br>Tattoo Removal</span>
    </div>

    <h1 class="employee-name">Melissa Thornbury</h1>
    <p class="employee-title">Chief Executive Offer</p>

    <address class="contact-details">
      <div class="address">
        <div>4615 Oakmere Pkwy, Suite 210</div>
        <div>Raleigh, NC 27654</div>
      </div>
      <div>M: 919.537.2846</div>
      <div>W: 919.362.4178</div>
      <div>F: 919.685.3907</div>
      <div>mthornbury@brightlinetattooremoval.example</div>
      <div>www.<strong>brightlinetattooremoval</strong>.example</div>
    </address>
  </section>
</body>
</html>
```